Homepage mockup for RoutineVerdict.com

I would like a homepage mockup of routineverdict.com.

Basically what the site does, is it allows a person to upload a video of a gymnastics routine and our certified judges will judge the routine providing a score, as well as provide a critique and feedback as to why they gave you that score. Many times people don't know why they got the score they did at a gymnastics competition, so this site aims to provide reasoning behind it.

I have started to design the homepage myself (see attached), and like it, but I'd like a professional to finish the layout, or even come up with something really wow and original. I like clean, typically simple design.

THIS IS AN OLD VERSION OF THE SITE (http://esite.kelpradia.com/) This should only be used so you can get an idea of what the site is about. I DO NOT want the new site to look like this, but the basic concept and content remains the same.

DESIGNER FILES CAN BE DOWNLOADED HERE (http://kelpradia.com/files.aspx)

Target Market(s)

Gymnastic type people, parents of gymnasts, coaches, etc.

Industry/Entity Type

It Professional

Requirements
Must have
• -Routine verdict logo (provided)
-Not required, but I have attached the main photo I used in my mockup (AI File)
*A step by step graphic(s) depicting the process for a user. A How it works sort of explanation. Should be eye catching, not just text.

-Step 1: Videotape your gymnastic routine.
-Step 2: Create an account and share us your video.
-Step 3: Our certified judges will score and critique your routine, fully explaining the reasons behind their score.

```html
<!DOCTYPE html>
<html lang="en">
<head>
<meta charset="utf-8">
<title>Routine Verdict</title>
<link href="https://fonts.googleapis.com/css2?family=Maven+Pro:wght@400;500;600;700&display=swap" rel="stylesheet">
<style>
:root{
  --ink:#333638;
  --header:#2c2e30;
  --header-light:#3a4047;
  --red:#c2363d;
  --red-dark:#9a0f12;
  --blue:#3b78b4;
  --blue-dark:#2a5f95;
  --steel:#45637c;
  --muted:#a9a9a9;
  --line:#d8d8d8;
  --beam:#e6d6c2;
  --white:#fff;
}
*{box-sizing:border-box;margin:0;padding:0}
html,body{width:1200px;height:983px;overflow:hidden}
body{font-family:"Maven Pro",Arial,sans-serif;color:var(--ink);background:var(--white);position:relative}

.site-header{position:absolute;left:0;top:0;width:1200px;height:125px;background:radial-gradient(ellipse at 20% 40%,var(--header-light),var(--header) 60%)}
.brand{position:absolute;left:162px;top:44px;display:flex;align-items:center;gap:10px}
.brand-mark{width:13px;height:13px;border-radius:50%;background:var(--red)}
.brand-name{font-size:30px;font-weight:700;color:var(--white);letter-spacing:-.5px}
.blog-tab{position:absolute;left:973px;top:0;width:117px;height:32px;background:linear-gradient(var(--blue),var(--blue-dark));color:var(--white);font-size:13px;font-weight:500;text-align:center;line-height:26px;border-radius:0 0 3px 3px}
.main-nav{position:absolute;left:500px;top:58px;width:590px;height:47px;background:linear-gradient(#fff,#e9e9e9);transform:skewX(-4deg);border-radius:3px;box-shadow:0 2px 4px rgba(0,0,0,.3)}
.main-nav ul{list-style:none;display:flex;transform:skewX(4deg);height:100%;align-items:center;padding-left:43px}
.main-nav li{font-size:16px;color:#222;margin-right:37px;letter-spacing:-.2px}
.main-nav li:last-child{margin-right:0}

.hero{position:absolute;left:0;top:125px;width:1200px;height:405px;background:linear-gradient(#eeeeee,#fafafa 60%,#f2f2f2)}
.beam{position:absolute;left:0;top:485px;width:1200px;height:45px;background:linear-gradient(#d9c6ac,var(--beam) 30%,#f3ebe0 70%,#cdb899);box-shadow:0 3px 5px rgba(0,0,0,.15)}
.video{position:absolute;left:138px;top:162px;width:402px;height:269px;border:4px solid #5a5c5f;background:linear-gradient(#3a2c4a,#27376e 55%,#3a3f8a 85%,#6e5a48)}
.video-play{position:absolute;left:165px;top:98px;width:72px;height:72px;border-radius:50%;background:rgba(40,40,40,.55)}
.video-play svg{position:absolute;left:24px;top:18px}
.video-shadow{position:absolute;left:150px;top:440px;width:380px;height:25px;border-radius:50%;background:radial-gradient(ellipse,rgba(0,0,0,.35),rgba(0,0,0,0) 70%)}
.hero-photo{position:absolute;left:850px;top:190px;width:300px;height:310px;background:radial-gradient(ellipse at 50% 45%,rgba(200,170,150,.8),rgba(90,75,70,.5) 35%,rgba(240,240,240,0) 68%)}
.hero-title{position:absolute;left:580px;top:160px;font-size:31px;line-height:31px;color:var(--red);font-weight:400;width:360px;letter-spacing:-.3px}
.hero-steps{position:absolute;left:571px;top:243px;list-style:none}
.hero-steps li{position:relative;height:51px;padding-left:57px}
.num{position:absolute;left:0;top:0;width:44px;height:44px;border-radius:50%;background:var(--blue);color:var(--white);font-weight:700;font-size:20px;text-align:center;line-height:44px}
.hero-steps h3{font-size:20px;font-weight:400;color:var(--steel);line-height:22px;padding-top:9px;letter-spacing:-.3px}
.hero-steps p{font-size:11.5px;color:var(--muted);line-height:15px}

.steps{position:absolute;left:125px;top:602px;width:644px;height:126px;border:1px solid var(--line);border-radius:9px;background:linear-gradient(#fff,#f0f0f0);display:flex}
.step{position:relative;border-right:1px solid var(--line);padding:60px 0 0 34px;font-size:21px;line-height:24px;color:#444;white-space:nowrap;letter-spacing:-.3px}
.step-1{width:211px}
.step-2{width:222px}
.step-3{flex:1;border-right:0;letter-spacing:-.7px}
.step-icon{position:absolute;top:-30px;left:50%;width:100px;height:78px;margin-left:-58px;border-radius:12px}
.icon-upload{background:linear-gradient(135deg,#555,#888 60%,#3d9ad6)}
.icon-judges{background:linear-gradient(#c86b3e,#5a8cc0)}
.icon-thumb{background:linear-gradient(135deg,#e2a57e,#3c70a8);width:80px;margin-left:-48px}
.plus{position:absolute;width:44px;height:44px}
.step-label{position:absolute;top:737px;font-size:22px;color:var(--steel);width:200px;text-align:center}
.btn{position:absolute;height:52px;border-radius:3px;color:var(--white);font-size:18px;font-weight:500;text-align:center;line-height:50px;box-shadow:0 0 0 2px #ddd}
.btn-red{background:linear-gradient(#d1191c,var(--red-dark))}
.btn-blue{background:linear-gradient(#4f8bc4,var(--blue-dark))}

.login{position:absolute;left:788px;top:601px;width:291px;height:242px;border:1px solid #ddd;background:#f6f6f6;box-shadow:0 2px 4px rgba(0,0,0,.12)}
.login h4{font-size:15px;font-weight:500;color:#666;padding:22px 0 0 25px;height:51px;border-bottom:1px solid #e3e3e3}
.login .close{position:absolute;right:19px;top:14px;font-size:24px;color:#bbb}
.field{position:absolute;left:16px;width:262px;height:31px;border:1px solid #ddd;background:var(--white);font-size:11px;color:#888;padding-left:19px;line-height:29px}
.login-foot{position:absolute;left:0;top:164px;width:100%;border-top:1px solid #e3e3e3}
.social-box{position:absolute;left:18px;top:31px;width:16px;height:16px;background:var(--blue)}
.mini{position:absolute;top:22px;height:32px;border-radius:2px;color:var(--white);font-size:12px;font-weight:600;text-align:center;line-height:30px;box-shadow:0 0 0 2px #e2e2e2}

.site-footer{position:absolute;left:0;top:927px;width:1200px;height:56px;background:var(--header);color:var(--white);font-size:13.5px}
.copyright{position:absolute;left:126px;top:20px}
.foot-nav{position:absolute;right:117px;top:19px;font-size:14.5px}
.foot-nav span{margin:0 5px;color:#ccc}
</style>
</head>
<body>
<header class="site-header">
  <div class="brand"><span class="brand-mark"></span><span class="brand-name">Routine Verdict</span></div>
  <div class="blog-tab">Read ur Blog !</div>
  <nav class="main-nav"><ul><li>Home</li><li>FAQ</li><li>Sample</li><li>Critique</li><li>Members Area</li><li>About</li></ul></nav>
</header>

<section class="hero"></section>
<div class="hero-photo" role="img" aria-label="Photo of a gymnast in a handstand on the balance beam"></div>
<div class="beam"></div>
<div class="video-shadow"></div>
<div class="video" role="img" aria-label="Video still of a gymnast's beam routine with score cards">
  <div class="video-play"><svg width="28" height="36" viewBox="0 0 28 36"><path d="M0 0L28 18L0 36Z" fill="#ddd"/></svg></div>
</div>
<h1 class="hero-title">Being Judged has never been Easier</h1>
<ol class="hero-steps">
  <li><span class="num">1</span><h3>Record your routine</h3><p>Videotape your gymnastic routine.</p></li>
  <li><span class="num">2</span><h3>Sign Up &amp; Upload</h3><p>Create an account and share us your video.</p></li>
  <li><span class="num">3</span><h3>Get the Why</h3><p>Our certified judges will score and critique<br>your routine, fully explaining the reasons<br>behind their score.</p></li>
</ol>

<div class="steps">
  <div class="step step-1"><div class="step-icon icon-upload" role="img" aria-label="Illustration of a video folder with a download arrow"></div>Upload Your<br>Video</div>
  <div class="step step-2"><div class="step-icon icon-judges" role="img" aria-label="Illustration of a panel of judges"></div>We'll judge your<br>routine</div>
  <div class="step step-3"><div class="step-icon icon-thumb" role="img" aria-label="Illustration of a thumbs-up hand"></div>Get the “why” &amp;<br>much, much more!</div>
</div>
<svg class="plus" style="left:315px;top:646px" viewBox="0 0 44 44"><path d="M15 0h14v15h15v14H29v15H15V29H0V15h15z" fill="#cfcfcf"/></svg>
<svg class="plus" style="left:537px;top:646px" viewBox="0 0 44 44"><path d="M15 0h14v15h15v14H29v15H15V29H0V15h15z" fill="#cfcfcf"/></svg>
<div class="step-label" style="left:128px">Step 1</div>
<div class="step-label" style="left:350px">Step 2</div>
<div class="step-label" style="left:561px">Step 3</div>
<div class="btn btn-red" style="left:127px;top:788px;width:182px">Get Judged Now ?</div>
<div class="btn btn-blue" style="left:328px;top:788px;width:191px">Sign Up Today</div>

<aside class="login">
  <h4>Already Member?&nbsp; Sign In Now</h4>
  <span class="close">×</span>
  <div class="field" style="top:74px">Your e-mail...</div>
  <div class="field" style="top:111px">Password...</div>
  <div class="login-foot">
    <span class="social-box"></span>
    <div class="mini btn-red" style="left:54px;width:80px">Sign Up</div>
    <div class="mini btn-blue" style="left:165px;width:80px">Log In</div>
  </div>
</aside>

<footer class="site-footer">
  <div class="copyright">Copyright 2010 , Routine Verdict. All rights reserved.</div>
  <div class="foot-nav">Home<span>|</span>FAQ<span>|</span>Sample<span>|</span>Critique<span>|</span>Members Area<span>|</span>About</div>
</footer>
</body>
</html>
```